Business card design Needed for new logo / Construction business, home extensions and new builds

We need a business card design using our new logo files which i will attach to this project :)

We are a small construction business specialising in home extensions, new builds and property development. We are very ambitious and would appreciate professional and elegant designs for our new business card.

Very serious about using the services on MakerQuarry and recently acquired our new logo from here :)

Please get involved, i will feedback when i can as i am very busy but can respond daily, thanks

Target Market(s)

People that want to build onto their houses, new building developments or adding too their existing property

Industry/Entity Type

Construction

Contact Information for Business Card

Renwick Tolliver Construction, Lionel Ashby (Managing Director), Tel 07822254961, email - info@renwick-tolliver, www.renwick-tolliver.co.uk

Colors

Designer to choose colors to be used in the design.

Requirements
Must have
• I like a deep grey on the back please. A lot of you have provided black from and back, try mixing things up a little. The black looks cool 😎 Thanks

```html
<!DOCTYPE html>
<html lang="en">
<head>
<meta charset="utf-8">
<title>Renwick Tolliver Construction – Business Card</title>
<link href="https://fonts.googleapis.com/css2?family=Cinzel:wght@600&family=Montserrat:wght@400;700&display=swap" rel="stylesheet">
<style>
  :root {
    --backdrop: #474747;
    --backdrop-dark: #3a3a3a;
    --card-front: #0e0e0e;
    --card-back: #1a1a1a;
    --gold: #d9a531;
    --white: #f4f4f4;
  }
  * { margin: 0; padding: 0; box-sizing: border-box; }
  html, body { width: 1200px; height: 801px; overflow: hidden; }
  body {
    background: radial-gradient(ellipse at 40% 20%, var(--backdrop) 0%, var(--backdrop-dark) 100%);
    font-family: "Montserrat", sans-serif;
    position: relative;
  }
  .card {
    position: absolute;
    top: 246px;
    width: 540px;
    height: 309px;
    border-radius: 18px;
    border: 3px solid var(--gold);
    overflow: hidden;
    box-shadow: 0 14px 30px rgba(0,0,0,.45);
  }
  .card--front { left: 40px; background: var(--card-front); }
  .card--back { left: 620px; background: var(--card-back); }

  /* front */
  .accent-tab {
    position: absolute; top: 0; right: 34px;
    width: 40px; height: 22px; background: var(--gold);
  }
  .holder {
    position: absolute; top: 34px; right: 34px; text-align: right;
  }
  .holder__name {
    color: var(--gold); font-weight: 700; font-size: 19px; letter-spacing: .5px;
  }
  .holder__title {
    color: var(--white); font-size: 12px; margin-top: 3px; letter-spacing: .4px;
  }
  .feature-mark {
    position: absolute; right: 34px; top: 118px; text-align: right;
    font-family: "Cinzel", serif; font-weight: 600; color: var(--gold);
    font-size: 30px; line-height: 1.1;
  }
  .brand {
    position: absolute; left: 30px; top: 118px;
    display: flex; align-items: center; gap: 10px;
  }
  .brand__square { width: 14px; height: 14px; background: var(--gold); }
  .brand__name {
    font-family: "Cinzel", serif; font-weight: 600; color: var(--gold);
    font-size: 15px; line-height: 1.15;
  }
  .address {
    position: absolute; left: 30px; top: 176px;
    color: var(--white); font-size: 12px; line-height: 1.45;
  }
  .contacts {
    position: absolute; left: 30px; top: 222px; list-style: none;
    color: var(--white); font-size: 12px;
  }
  .contacts li { display: flex; align-items: center; gap: 8px; height: 20px; }
  .contacts svg { width: 13px; height: 13px; flex: none; }

  /* back */
  .back-brand {
    position: absolute; inset: 0;
    display: flex; flex-direction: column; align-items: center; justify-content: center; gap: 18px;
  }
  .back-brand__square { width: 44px; height: 44px; background: var(--gold); }
  .back-brand__name {
    font-family: "Cinzel", serif; font-weight: 600; color: var(--gold);
    font-size: 30px; text-align: center; line-height: 1.15;
  }
</style>
</head>
<body>
  <section class="card card--front" aria-label="Business card front">
    <div class="accent-tab"></div>
    <div class="holder">
      <p class="holder__name">LIONEL ASHBY</p>
      <p class="holder__title">Managing Director</p>
    </div>
    <p class="feature-mark">Renwick<br>Tolliver</p>
    <div class="brand">
      <span class="brand__square"></span>
      <p class="brand__name">Renwick Tolliver<br>Construction</p>
    </div>
    <p class="address">Your address, City<br>State, Zip 1234</p>
    <ul class="contacts">
      <li>
        <svg viewBox="0 0 16 16" aria-hidden="true"><circle cx="8" cy="8" r="8" fill="var(--gold)"/><path d="M5 4.5l1.6-.3.9 2-1 .8a5 5 0 002.5 2.5l.8-1 2 .9-.3 1.6C9 11.5 4.5 7 5 4.5z" fill="#0e0e0e"/></svg>
        07700 900461
      </li>
      <li>
        <svg viewBox="0 0 16 16" aria-hidden="true"><circle cx="8" cy="8" r="8" fill="var(--gold)"/><rect x="4" y="5" width="8" height="6" fill="#0e0e0e"/><path d="M4 5l4 3.2L12 5" stroke="var(--gold)" fill="none"/></svg>
        info@renwick-tolliver
      </li>
      <li>
        <svg viewBox="0 0 16 16" aria-hidden="true"><circle cx="8" cy="8" r="8" fill="var(--gold)"/><circle cx="8" cy="8" r="4" fill="none" stroke="#0e0e0e"/><path d="M4 8h8M8 4c-2 2.5-2 5.5 0 8M8 4c2 2.5 2 5.5 0 8" stroke="#0e0e0e" fill="none" stroke-width=".8"/></svg>
        www.renwick-tolliver.co.uk
      </li>
    </ul>
  </section>

  <section class="card card--back" aria-label="Business card back">
    <div class="back-brand">
      <span class="back-brand__square"></span>
      <p class="back-brand__name">Renwick Tolliver<br>Construction</p>
    </div>
  </section>
</body>
</html>
```